Small Business Consulting Firm Needs Letterhead

We need a letterhead for our company "Brightpath Plus". Our company does outbound calling and mailing to business owner's companies who have taken high interest loans. These loans tend to put these businesses in a big financial bind short term, and we help them find better financial options. We would like the design to match our colors of our logo. Headers and footers would look nice, but we are open. We would want it to include our address, website, phone, and email info. Our address - 2000 E. Lamar Blvd. Suite 600Website - www.safeguardtoday.comEmail - info@safeguardtoday.comPhone - 855-726-1938
Industry/Entity Type
Financial Planning
Look and feel
Each slider illustrates characteristics of the customer's brand and the style your logo design should communicate.

```html
<!DOCTYPE html>
<html lang="en">
<head>
<meta charset="utf-8">
<title>Brightpath Plus Letterhead</title>
<link href="https://fonts.googleapis.com/css2?family=Open+Sans:wght@400;600&family=Lato:wght@400;700&display=swap" rel="stylesheet">
<style>
  :root {
    --blue: #0b6fb5;
    --green: #6db33f;
    --ink: #3c3c3c;
    --ink-strong: #222;
    --rule: #b8b8b8;
    --paper: #ffffff;
  }
  html, body { margin: 0; padding: 0; overflow: hidden; background: var(--paper); }
  .letterhead {
    position: relative;
    width: 1040px;
    height: 1200px;
    background: var(--paper);
    font-family: "Open Sans", sans-serif;
    color: var(--ink);
    overflow: hidden;
  }
  .edge-band { position: absolute; top: 0; bottom: 0; width: 14px; }
  .edge-band-left { left: 0; background: var(--blue); }
  .edge-band-right { right: 0; background: var(--green); }
  .brand {
    position: absolute;
    top: 39px;
    left: 0;
    width: 100%;
    text-align: center;
  }
  .brand-square {
    display: block;
    width: 44px;
    height: 44px;
    margin: 0 auto 38px;
    background: var(--green);
  }
  .brand-name {
    font-size: 19px;
    font-weight: 400;
    letter-spacing: 2.5px;
    line-height: 20px;
    color: var(--ink-strong);
    text-transform: uppercase;
  }
  .body {
    position: absolute;
    left: 98px;
    width: 840px;
    font-size: 16px;
    line-height: 20px;
  }
  .issue-date { top: 216px; }
  .recipient { top: 252px; line-height: 18px; }
  .salutation { top: 356px; }
  .letter-text { line-height: 27px; text-align: justify; hyphens: auto; }
  .letter-text.p1 { top: 409px; }
  .letter-text.p2 { top: 571px; }
  .letter-text.p3 { top: 679px; }
  .closing { top: 814px; }
  .signatory { top: 890px; }
  .signatory-name { font-size: 19px; font-weight: 600; color: var(--ink-strong); margin: 0 0 8px; line-height: 24px; }
  .signatory-title { margin: 0; }
  .footer {
    position: absolute;
    left: 103px;
    width: 833px;
    top: 1119px;
    font-family: "Lato", sans-serif;
    text-align: center;
    color: var(--ink-strong);
  }
  .footer-address { font-size: 17px; padding-bottom: 6px; border-bottom: 1.5px solid var(--rule); }
  .footer-contact { font-size: 17px; margin-top: 7px; }
  .label { color: var(--blue); font-weight: 700; }
  .web { color: var(--blue); }
  .web-accent { color: var(--green); }
</style>
</head>
<body>
<div class="letterhead">
  <div class="edge-band edge-band-left"></div>
  <div class="edge-band edge-band-right"></div>

  <header class="brand">
    <span class="brand-square"></span>
    <div class="brand-name">Brightpath Plus</div>
  </header>

  <div class="body issue-date">Issuing Date: May 5, 2018</div>

  <div class="body recipient">
    Name Of Employee Mr. XYZABC<br>
    Address of Employee<br>
    Address Line 2 etc..
  </div>

  <div class="body salutation">Dear Mr.XYZABC</div>

  <div class="body letter-text p1">Lorem Ipsum has been the industry's standard dummy text ever since the 1500s, when an unknown printer took a galley of type and scrambled it to make a type specimen book. It has survived not only five centuries, but also the leap into electronic typesetting, remaining essentially unchanged. It was popularised in the 1960s with the release of Lettersheet sheets containing Lorem Ipsum passages, and more recently with desktop publishing software like Pagecraft Studio including versions of Lorem Ipsum.</div>

  <div class="body letter-text p2">Lorem Ipsum is simply dummy text of the printing and typesetting industry. Lorem Ipsum has been the industry's standard dummy text ever since the 1500s, when an unknown printer took a galley of type and scrambled it to make a type specimen book.</div>

  <div class="body letter-text p3">It has survived not only five centuries, but also the leap into electronic typesetting, remaining essentially unchanged. It was popularised in the 1960s with the release of Lettersheet sheets containing Lorem IpsumIpsum passages.</div>

  <div class="body closing">Yours Sincerely</div>

  <div class="body signatory">
    <p class="signatory-name">Marcus Hollen</p>
    <p class="signatory-title">Managing Director</p>
  </div>

  <footer class="footer">
    <div class="footer-address">4170 W. Corwin Ave. Suite 310</div>
    <div class="footer-contact">
      <span class="label">P:</span> 855-726-1938 &nbsp;|&nbsp;<span class="label">E:</span> info@brightpathplus.com |
      <span class="web">www.<span class="web-accent">brightpathplus</span>.com</span>
    </div>
  </footer>
</div>
</body>
</html>
```